Bry7Legal Letterhead

Need a new letterhead for my law firm.
IDENTIFYING INFORMATION BELOW:
Anselmo R Quintara III
Attorney at Law
Address: 2847 Larkspur Blvd, Ste 300, Dallas, TX 75204
Phone: 877-482-6017
Fax: 469-738-1452
Email: bry@bry7legal.example
Website: www.bry7legal.example

Colors
0054AA
0677BA
7BADD7
CADEEF
E8F1F8

Requirements
Must have
• Logo needs to be on the letterhead, along with identifying information which is included in the project description.

```html
<!DOCTYPE html>
<html lang="en">
<head>
<meta charset="utf-8">
<title>Bry7Legal Letterhead</title>
<link rel="stylesheet" href="https://fonts.googleapis.com/css2?family=Lato:wght@400;700&family=Open+Sans:wght@400&display=swap">
<style>
  :root {
    --blue-deep: #0054AA;
    --blue-mid: #0677BA;
    --blue-light: #7BADD7;
    --blue-pale: #CADEEF;
    --blue-mist: #E8F1F8;
    --ink: #111111;
    --text: #4a4a4a;
    --sheet: #ffffff;
    --backdrop: #e4e4e4;
    --band: #000000;
  }
  * { box-sizing: border-box; margin: 0; padding: 0; }
  html, body { width: 1040px; height: 1200px; overflow: hidden; background: var(--backdrop); }
  .sheet {
    position: absolute; left: 54px; top: 0;
    width: 932px; height: 1200px;
    background: var(--sheet);
    font-family: "Open Sans", Arial, sans-serif;
    color: var(--text);
  }
  .sheet-shapes { position: absolute; inset: 0; width: 932px; height: 1200px; }
  .brand {
    position: absolute; left: 106px; top: 56px;
    display: flex; align-items: center; gap: 12px;
    font-family: "Lato", Arial, sans-serif; font-weight: 400;
    font-size: 32px; line-height: 36px; letter-spacing: 0.5px;
    color: var(--blue-deep);
  }
  .brand-square { width: 14px; height: 14px; background: var(--blue-deep); }
  .header-divider {
    position: absolute; left: 605px; top: 40px; width: 2px; height: 62px;
    background: #bdbdbd;
  }
  .attorney { position: absolute; left: 627px; top: 46px; font-family: "Lato", Arial, sans-serif; }
  .attorney-name { font-size: 22px; line-height: 26px; font-weight: 700; color: var(--blue-deep); }
  .attorney-role { font-size: 17px; line-height: 18px; color: var(--ink); }
  .letter { position: absolute; left: 88px; width: 752px; font-size: 14px; }
  .letter-date { top: 235px; }
  .letter-recipient { top: 270px; line-height: 18px; }
  .letter-greeting { top: 375px; }
  .letter-body { top: 425px; line-height: 26.7px; text-align: justify; hyphens: auto; }
  .letter-body p + p { margin-top: 26.7px; }
  .letter-closing { top: 833px; }
  .signature {
    position: absolute; left: 88px; top: 870px; width: 220px; height: 28px;
    background: linear-gradient(90deg, var(--blue-mist), #f2f2f2);
  }
  .signer { position: absolute; left: 88px; top: 910px; }
  .signer-name { font-size: 18.5px; line-height: 26px; color: #222; }
  .signer-title { font-size: 14.5px; line-height: 24px; }
  .footer-address {
    position: absolute; left: 0; right: 0; top: 1122px; text-align: center;
    font-family: "Lato", Arial, sans-serif; font-size: 17px; line-height: 22px; color: var(--ink);
  }
  .footer-contacts {
    position: absolute; left: 0; right: 0; top: 1163px; text-align: center;
    font-family: "Lato", Arial, sans-serif; font-size: 17px; line-height: 22px; color: #fff;
  }
  .footer-contacts .label { color: var(--blue-mid); }
</style>
</head>
<body>
  <main class="sheet">
    <svg class="sheet-shapes" viewBox="0 0 804 1035" preserveAspectRatio="none" aria-hidden="true">
      <defs>
        <linearGradient id="corner-blue" x1="0" y1="0" x2="0.3" y2="1">
          <stop offset="0" stop-color="#0A8CD0"/>
          <stop offset="1" stop-color="#0054AA"/>
        </linearGradient>
      </defs>
      <path d="M0 0 H650 V3 C420 4 210 8 125 38 C45 70 6 140 0 210 Z" fill="url(#corner-blue)"/>
      <path d="M804 835 C792 930 705 985 560 990 L0 993 V1035 H804 Z" fill="#000"/>
    </svg>

    <div class="brand"><span class="brand-square"></span><span>Bry7Legal</span></div>

    <div class="header-divider"></div>
    <div class="attorney">
      <div class="attorney-name">Anselmo R Quintara III</div>
      <div class="attorney-role">Attorney at Law</div>
    </div>

    <p class="letter letter-date">Issuing Date: May 5, 2018</p>
    <div class="letter letter-recipient">
      <p>Name Of Employee Mr. XYZABC</p>
      <p>Address of Employee</p>
      <p>Address Line 2 etc..</p>
    </div>
    <p class="letter letter-greeting">Dear Mr.XYZABC</p>
    <div class="letter letter-body">
      <p>Lorem Ipsum has been the industry's standard dummy text ever since the 1500s, when an unknown printer took a galley of type and scrambled it to make a type specimen book. It has survived not only five centuries, but also the leap into electronic typesetting, remaining essentially unchanged. It was popularised in the 1960s with the release of Linotrace sheets containing Lorem Ipsum passages, and more recently with desktop publishing software like Alder PageSmith including versions of Lorem Ipsum.</p>
      <p>Lorem Ipsum is simply dummy text of the printing and typesetting industry. Lorem Ipsum has been the industry's standard dummy text ever since the 1500s, when an unknown printer took a galley of type and scrambled it to make a type specimen book.</p>
      <p>It has survived not only five centuries, but also the leap into electronic typesetting, remaining essentially unchanged. It was popularised in the 1960s with the release of Linotrace sheets containing Lorem Ipsum passages.</p>
    </div>
    <p class="letter letter-closing">Yours Sincerely</p>
    <div class="signature" role="img" aria-label="Handwritten signature of Dorian Wexley"></div>
    <div class="signer">
      <p class="signer-name">Dorian Wexley</p>
      <p class="signer-title">Managing Director</p>
    </div>

    <p class="footer-address">2847 Larkspur Blvd, Ste 300, Dallas, TX 75204</p>
    <p class="footer-contacts">
      <span class="label">P:</span> 877-482-6017 &nbsp;|&nbsp; <span class="label">F:</span> 469-738-1452 | <span class="label">E:</span> bry@bry7legal.example &nbsp;|&nbsp; <span class="label">W:</span> www.bry7legal.example
    </p>
  </main>
</body>
</html>
```